Photography business - business card design quick turn around

Create a business card design for me please. I actually need the final design back before the end of Sunday 13th May 7pm GMT. Sorry for the short notice.

Photoshop artwork template uploaded with artwork guidelines including printer profiles and other mandatory specifications. Only one side of the business card is required as the other side will be an image.

The design is required as an unflattened PSD file so that I can edit the text if I need to.

My brand colours are white and the teal you see in the logo. Occasionally I also use a dark grey on my website (I don't mind the shade of grey as appreciate grey on teal would be a different grey, to the grey I use on white on the website, so just use a shade of grey that matches). Font can be as the font for the logo or if you prefer I am open to another sans serif, easily legible font. Ideally font size will be 12+.Please do not use capital letters for text. I prefer everything to be lower case, if possible.

Thank you.

Lena

Target Market(s)

Other business owners who may refer me and families

Industry/Entity Type

Photographer

Contact Information for Business Card

Silver Kettle Photography Logo
Sub text: family portraiture, captured with love

Contact information, ideally using simple icons to represent email / website / facebook / instagram / pinterest

email: lena@silverkettlephotography.co.uk
website: silverkettlephotography.co.uk
facebook: @silverkettlephotography
pinterest: pinterest.com/silverkettlepho
instagram: @silverkettle_photography
mobile/telephone: 07713460291

If there is too much text then please drop the instagram and pinterest information.

Font styles to use
Sans Serif

Colors
33b8a4

Requirements
Must have
• Logo
• Contact details as listed above
• sub text
Nice to have
• Instagram and Pinterest contact details
• Nice to have icons to represent website / phone / facebook etc followered by the handle where relevant

```html
<!DOCTYPE html>
<html lang="en">
<head>
<meta charset="utf-8">
<title>Silver Kettle Photography – Business Card</title>
<link rel="stylesheet" href="https://fonts.googleapis.com/css2?family=Raleway:ital,wght@0,400;0,500;0,700;1,400&display=swap">
<style>
  :root {
    --teal: #45bfb1;
    --white: #ffffff;
    --grey: #7d7d7d;
    --bg-light: #4a4a4a;
    --bg-dark: #161616;
  }
  * { margin: 0; padding: 0; box-sizing: border-box; }
  html, body { width: 1189px; height: 1200px; overflow: hidden; }
  body {
    position: relative;
    font-family: "Raleway", sans-serif;
    background: radial-gradient(ellipse 70% 55% at 50% 38%, var(--bg-light) 0%, #2c2c2c 55%, var(--bg-dark) 100%);
  }
  .card {
    position: absolute;
    width: 437px;
    height: 668px;
    border-radius: 30px;
    overflow: hidden;
    box-shadow: 0 6px 14px rgba(0,0,0,0.55);
  }

  /* front */
  .card-front { left: 121px; top: 280px; background: var(--teal); }
  .front-block {
    position: absolute;
    left: -6px; top: 272px;
    width: 474px; height: 120px;
    transform: rotate(-90deg);
    transform-origin: 237px 60px;
    color: var(--white);
  }
  .front-mark {
    position: absolute; left: 28px; top: 0;
    width: 76px; height: 76px; border-radius: 50%;
    border: 6px solid var(--white);
  }
  .front-name {
    position: absolute; left: 135px; top: 6px;
    font-size: 45px; font-weight: 500; line-height: 1;
    white-space: nowrap; letter-spacing: 0.3px;
  }
  .front-sub {
    position: absolute; left: 135px; top: 51px;
    font-size: 22px; font-weight: 700; line-height: 1;
    letter-spacing: 9.4px; white-space: nowrap;
  }
  .front-tagline {
    position: absolute; left: 59px; top: 97px;
    font-size: 19.5px; font-style: italic; line-height: 1;
    letter-spacing: 0.6px; white-space: nowrap;
  }

  /* back */
  .card-back { left: 577px; top: 284px; background: var(--white); }
  .brand-mark {
    position: absolute; left: 163px; top: 61px;
    width: 110px; height: 110px; border-radius: 50%;
    border: 7px solid var(--teal);
  }
  .back-brand {
    position: absolute; left: 100px; top: 204px;
    color: var(--teal); line-height: 1; white-space: nowrap;
  }
  .back-name { display: block; font-size: 32px; font-weight: 500; }
  .back-sub { display: block; font-size: 17px; font-weight: 700; letter-spacing: 5.6px; margin-top: 1px; }
  .back-tagline {
    position: absolute; left: 0; right: 0; top: 259px;
    text-align: center; font-style: italic; font-size: 19px;
    letter-spacing: 1px; color: var(--grey); white-space: nowrap;
  }
  .contact-list { position: absolute; left: 0; right: 0; top: 320px; list-style: none; }
  .contact-item { height: 51px; text-align: center; }
  .divider { display: block; margin: 0 auto; }
  .contact-text { display: block; font-size: 19px; color: var(--grey); margin-top: 1px; line-height: 22px; white-space: nowrap; }
  .web-band {
    position: absolute; left: 0; right: 0; bottom: 0; height: 47px;
    background: var(--teal); color: var(--white);
    font-size: 20px; text-align: center; line-height: 45px; white-space: nowrap;
  }
</style>
</head>
<body>
  <section class="card card-front" aria-label="Card front">
    <div class="front-block">
      <div class="front-mark"></div>
      <span class="front-name">SILVER KETTLE</span>
      <span class="front-sub">photography</span>
      <span class="front-tagline">family portraiture, captured with love</span>
    </div>
  </section>

  <section class="card card-back" aria-label="Card back">
    <div class="brand-mark"></div>
    <div class="back-brand">
      <span class="back-name">SILVER KETTLE</span>
      <span class="back-sub">photography</span>
    </div>
    <p class="back-tagline">family portraiture, captured with love</p>

    <ul class="contact-list">
      <li class="contact-item">
        <svg class="divider" width="220" height="24" viewBox="0 0 220 24">
          <path d="M0 12 L92 10.5 L92 13.5 Z M220 12 L128 10.5 L128 13.5 Z" fill="var(--teal)"/>
          <circle cx="110" cy="12" r="11" fill="none" stroke="var(--teal)" stroke-width="1.6"/>
          <rect x="105.5" y="5" width="9" height="14" rx="1.5" fill="none" stroke="var(--teal)" stroke-width="1.5"/>
          <line x1="108.5" y1="16.5" x2="111.5" y2="16.5" stroke="var(--teal)" stroke-width="1.2"/>
        </svg>
        <span class="contact-text">07713460291</span>
      </li>
      <li class="contact-item">
        <svg class="divider" width="220" height="24" viewBox="0 0 220 24">
          <path d="M0 12 L92 10.5 L92 13.5 Z M220 12 L128 10.5 L128 13.5 Z" fill="var(--teal)"/>
          <circle cx="110" cy="12" r="11" fill="none" stroke="var(--teal)" stroke-width="1.6"/>
          <rect x="103.5" y="7.5" width="13" height="9" fill="var(--teal)"/>
          <path d="M103.5 7.5 L110 12.5 L116.5 7.5" fill="none" stroke="var(--white)" stroke-width="1.2"/>
        </svg>
        <span class="contact-text">lena@silverkettlephotography.co.uk</span>
      </li>
      <li class="contact-item">
        <svg class="divider" width="220" height="24" viewBox="0 0 220 24">
          <path d="M0 12 L92 10.5 L92 13.5 Z M220 12 L128 10.5 L128 13.5 Z" fill="var(--teal)"/>
          <circle cx="110" cy="12" r="11" fill="none" stroke="var(--teal)" stroke-width="1.6"/>
        </svg>
        <span class="contact-text">@silverkettlephotography</span>
      </li>
      <li class="contact-item">
        <svg class="divider" width="220" height="24" viewBox="0 0 220 24">
          <path d="M0 12 L92 10.5 L92 13.5 Z M220 12 L128 10.5 L128 13.5 Z" fill="var(--teal)"/>
          <circle cx="110" cy="12" r="11" fill="none" stroke="var(--teal)" stroke-width="1.6"/>
        </svg>
        <span class="contact-text">pinshelf.net/silverkettlepho</span>
      </li>
      <li class="contact-item">
        <svg class="divider" width="220" height="24" viewBox="0 0 220 24">
          <path d="M0 12 L92 10.5 L92 13.5 Z M220 12 L128 10.5 L128 13.5 Z" fill="var(--teal)"/>
          <circle cx="110" cy="12" r="11" fill="none" stroke="var(--teal)" stroke-width="1.6"/>
        </svg>
        <span class="contact-text">@silverkettle_photography</span>
      </li>
    </ul>

    <div class="web-band">silverkettlephotography.co.uk</div>
  </section>
</body>
</html>
```